Webdesign für HALDEN STAHLWERK
Zielgruppe
Valkorin ist Ihr leistungsstarker und zuverlässiger Partner im Bereich Metallverarbeitung. Seit unserer Firmengründung im Jahr 2001 ist unser inhabergeführtes Unternehmen in Gornau bei Chemnitz kontinuierlich gewachsen und beschäftigt derzeit 20 engagierte und qualifizierte Mitarbeiter.
Mit der Einweihung unserer neuen Fertigungshalle 2010 haben wir unsere Produktionsfläche auf 1.400 m2 vergrößert und können Ihnen nun einen noch umfassenderen Service anbieten.
Von der CNC-gesteuerten Teilefertigung bis zu modernsten Schweiß-, Schneid-, und Bearbeitungsanlagen – für die Realisierung Ihrer individuellen Wünsche steht uns ein innovativer Maschinenpark zur Verfügung. Wir fertigen zuverlässig und termingerecht nach Ihren Plänen oder übernehmen bei Bedarf auch die gesamte Abwicklung Ihres Projektes – alles made in germany!
Das Unternehmen spricht ausschließlich B2B Kunden an.
Die Hauptleistungsbereiche sind:
- Stahl- und Palettenbau
- Blechbearbeitung
- Edelstahlbearbeitung
- Mechanische Fertigung
Aufgabenstellung
- Mitlaufende Kontaktleiste
- Integration der Social Media Kanäle
- Sehr modernes Auftreten
- Industrielles Design
- Verlinkung zum Partnerunternehmen https://www.valkorin-beispiel.de/ias/index.html

```html
<!DOCTYPE html>
<html lang="de">
<head>
<meta charset="utf-8">
<title>HALDEN STAHLWERK – Valkorin</title>
<link href="https://fonts.googleapis.com/css2?family=Outfit:wght@300;400;500;600;700;800&display=swap" rel="stylesheet">
<style>
:root{
  --ink:#0b1120;
  --topbar:#1b2331;
  --header:#0e1627;
  --navy:#0f1a45;
  --royal:#0f3b86;
  --blue:#3d8fe0;
  --blue-soft:#5aa2ea;
  --line:#2b3a74;
  --grey:#6c7383;
  --text:#1a1f2b;
  --white:#ffffff;
}
*{margin:0;padding:0;box-sizing:border-box}
html,body{width:1200px;height:4125px;overflow:hidden}
body{position:relative;font-family:'Outfit',sans-serif;color:var(--text);background:var(--white)}
.abs{position:absolute}
.eyebrow{position:absolute;font-size:10px;letter-spacing:1.6px;text-transform:uppercase;color:var(--blue);font-weight:500}
.heading{position:absolute;font-size:26px;font-weight:500;letter-spacing:.2px}
.rule{position:absolute;height:1px;background:var(--line)}
.rule-light{position:absolute;height:1px;background:#e3e6ec}
.btn{position:absolute;display:flex;align-items:center;justify-content:center;gap:8px;font-size:12px;border:1px solid;height:40px}
.btn svg{width:14px;height:10px}
.photo{position:absolute}

/* top bar */
.topbar{left:0;top:0;width:1200px;height:29px;background:var(--topbar);color:#cfd4dc;font-size:9px;letter-spacing:.6px}
.topbar span{position:absolute;top:9px}
.dot{position:absolute;width:10px;height:10px;border-radius:50%;background:#7d8696;top:9px}
/* header */
.header{left:0;top:29px;width:1200px;height:76px;background:var(--header)}
.logo{position:absolute;font-weight:800;color:var(--white);letter-spacing:-.5px}
.nav{position:absolute;top:28px;font-size:12px;color:var(--white)}
/* hero */
.hero{left:0;top:105px;width:1200px;height:495px;background:radial-gradient(ellipse at 55% 35%,#6d5a44 0%,#3a3936 35%,#1d2028 75%,#141821 100%)}
.hero-title{position:absolute;left:0;top:160px;width:1200px;text-align:center;color:var(--white);font-size:38px;font-weight:400;line-height:41px}
.side{position:absolute;left:1150px;width:50px;height:50px;background:var(--blue);display:flex;align-items:center;justify-content:center}
.vertical{position:absolute;left:1098px;top:370px;transform:rotate(-90deg);transform-origin:left top;color:#d6d9df;font-size:9px;letter-spacing:1.4px;white-space:nowrap}
/* navy */
.navy{left:0;top:600px;width:1200px;height:1085px;background:var(--navy)}
.card-label{position:absolute;background:var(--navy);color:var(--white);font-size:11px;letter-spacing:1.6px;line-height:14px;padding:12px 16px 0}
.body-text{position:absolute;font-size:10.5px;line-height:17px}
/* facts */
.num{position:absolute;width:200px;text-align:center;font-size:60px;font-weight:500;color:var(--blue);letter-spacing:-1px}
.num-label{position:absolute;width:200px;text-align:center;font-size:9px;letter-spacing:1.5px;font-weight:500}
.vdiv{position:absolute;width:1px;height:80px;background:#e3e6ec;top:1905px}
/* news */
.tag{position:absolute;height:20px;padding:0 10px;border-radius:10px;background:var(--blue);color:var(--white);font-size:8px;line-height:20px}
.news-title{position:absolute;font-size:12px;font-weight:500;letter-spacing:.3px}
.news-date{position:absolute;font-size:8.5px;color:#9aa0ab}
/* contact */
.contact-line{position:absolute;color:var(--white)}
/* footer */
.footer{left:0;top:3525px;width:1200px;height:600px;background:var(--ink)}
.fcol{position:absolute;font-size:10px;color:var(--white)}
.fcol h4{font-size:9.5px;letter-spacing:1.6px;color:var(--blue);font-weight:500;margin-bottom:16px}
.fcol p{margin-bottom:13px}
.sicon{position:absolute;width:16px;height:16px;border-radius:50%;background:var(--blue);top:4018px}
</style>
</head>
<body>

<!-- Top bar -->
<div class="abs topbar">
  <span style="left:40px">T: +49 3000 / 555 010 2</span>
  <span style="left:178px">E: INFO@VALKORIN-BEISPIEL.DE</span>
  <i class="dot" style="left:990px"></i><i class="dot" style="left:1022px"></i><i class="dot" style="left:1054px"></i><i class="dot" style="left:1086px"></i><i class="dot" style="left:1118px"></i><i class="dot" style="left:1150px"></i>
</div>

<!-- Header -->
<header class="abs header">
  <div class="logo" style="left:40px;top:20px;font-size:30px">VALKORIN</div>
  <div class="nav" style="left:530px">Home</div>
  <div class="nav" style="left:592px">Leistungen</div>
  <div class="nav" style="left:683px">Produkte</div>
  <div class="nav" style="left:763px">Fertigung</div>
  <div class="nav" style="left:846px">Qualifikation</div>
  <div class="nav" style="left:947px">Über Uns</div>
  <div class="btn" style="left:1062px;top:16px;width:98px;color:var(--blue);border-color:var(--blue)">Kontakt <svg viewBox="0 0 14 10"><path d="M0 5h12M8 1l4 4-4 4" stroke="currentColor" fill="none"/></svg></div>
</header>

<!-- Hero -->
<section class="abs hero" role="img" aria-label="Foto: CNC-Fräsmaschine bearbeitet ein Metallwerkstück mit Funkenflug">
  <div class="abs" style="left:40px;top:0;width:1px;height:463px;background:rgba(255,255,255,.25)"></div>
  <div class="abs" style="left:40px;top:463px;width:1070px;height:1px;background:rgba(255,255,255,.25)"></div>
  <h1 class="hero-title">Ihr zuverlässiger Partner im<br>Bereich der Metallverarbeitung</h1>
  <div class="btn" style="left:437px;top:260px;width:146px;background:var(--white);border-color:var(--white);color:var(--royal)">Angebot einholen <svg viewBox="0 0 14 10"><path d="M0 5h12M8 1l4 4-4 4" stroke="currentColor" fill="none"/></svg></div>
  <div class="btn" style="left:604px;top:260px;width:157px;border-color:var(--white);color:var(--white)">Jetzt mehr erfahren <svg viewBox="0 0 14 10"><path d="M0 5h12M8 1l4 4-4 4" stroke="currentColor" fill="none"/></svg></div>
  <div class="abs" style="left:1108px;top:40px;width:1px;height:65px;background:rgba(255,255,255,.5)"></div>
  <div class="abs" style="left:1108px;top:370px;width:1px;height:65px;background:rgba(255,255,255,.5)"></div>
  <div class="vertical">YOUR PARTNER OF EXCELLENCE IN METALWORK.</div>
  <svg class="abs" style="left:0;top:395px" width="1200" height="100"><polygon points="1130,100 1200,30 1200,100" fill="#0f1a45"/></svg>
</section>
<div class="side" style="top:265px"><svg width="20" height="20" viewBox="0 0 20 20" fill="none" stroke="#fff" stroke-width="1.4"><path d="M2 9l16-7-5 16-3-6z M10 12l8-10"/></svg></div>
<div class="side" style="top:325px"><svg width="20" height="20" viewBox="0 0 20 20" fill="none" stroke="#fff" stroke-width="1.4"><path d="M5 2l3 4-2 2c1 2 4 5 6 6l2-2 4 3-2 3C9 18 2 11 2 4z"/></svg></div>
<div class="side" style="top:385px"><svg width="20" height="20" viewBox="0 0 20 20" fill="none" stroke="#fff" stroke-width="1.4"><path d="M2 18h16M4 18V9h4v9M8 18V5h5v13M13 18v-6h4v6"/></svg></div>

<!-- Navy: Leistungen + Partner -->
<section class="abs navy"></section>
<div class="eyebrow" style="left:151px;top:678px">Leistungen</div>
<h2 class="heading" style="left:151px;top:696px;color:var(--white)">Unsere Leistungsbereiche</h2>
<div class="rule" style="left:505px;top:712px;width:530px;background:#2d4590"></div>
<div class="abs" style="left:1036px;top:704px;color:var(--blue);font-size:10px">×</div>

<div class="photo" style="left:151px;top:767px;width:211px;height:254px;background:linear-gradient(160deg,#4a4c52,#8a6a45 60%,#2a2c31);clip-path:polygon(0 0,88% 0,100% 12%,100% 100%,0 100%)" role="img" aria-label="Foto: Laserschneiden von Stahlplatten"></div>
<div class="photo" style="left:380px;top:767px;width:211px;height:254px;background:linear-gradient(160deg,#3a1f30,#b8442c 55%,#2a1b22);clip-path:polygon(0 0,88% 0,100% 12%,100% 100%,0 100%)" role="img" aria-label="Foto: Laserkopf schneidet Blech mit Funken"></div>
<div class="photo" style="left:609px;top:767px;width:211px;height:254px;background:linear-gradient(160deg,#dfe3e8,#a9b4c0 55%,#4b5a77);clip-path:polygon(0 0,88% 0,100% 12%,100% 100%,0 100%)" role="img" aria-label="Foto: Arbeiter mit Helm prüft Edelstahlrohre"></div>
<div class="photo" style="left:838px;top:767px;width:211px;height:254px;background:linear-gradient(160deg,#9aa3ad,#4e5a6b 55%,#23293a);clip-path:polygon(0 0,88% 0,100% 12%,100% 100%,0 100%)" role="img" aria-label="Foto: Mechaniker an einer Fertigungsmaschine"></div>
<div class="card-label" style="left:151px;top:995px;width:155px;height:40px">STAHL- UND<br>PALETTENBAU</div>
<div class="card-label" style="left:380px;top:995px;width:155px;height:40px">BLECH-<br>BEARBEITUNG</div>
<div class="card-label" style="left:609px;top:995px;width:155px;height:40px">EDELSTAHL-<br>BEARBEITUNG</div>
<div class="card-label" style="left:838px;top:995px;width:155px;height:40px">MECHANISCHE<br>FERTIGUNG</div>
<div class="btn" style="left:491px;top:1091px;width:182px;border-color:var(--white);color:var(--white)">Alle Leistungen ansehen <svg viewBox="0 0 14 10"><path d="M0 5h12M8 1l4 4-4 4" stroke="currentColor" fill="none"/></svg></div>

<div class="eyebrow" style="left:151px;top:1267px">Ihr zuverlässiger Partner</div>
<h2 class="heading" style="left:151px;top:1285px;color:var(--white);line-height:34px">Wir vereinen Qualität und<br>Kundenzufriedenheit</h2>
<p class="body-text" style="left:151px;top:1370px;width:330px;color:#d3d8e6">Lorem ipsum dolor sit amet consectetur. Risus risus dui commodo posuere aenean ac mauris sed. Morbi aliquam tincidunt nibh leo. Quam ipsum sapien mauris pharetra id convallis ac nunc venenatis. Blandit viverra nunc enim sagittis accumsan habitant. Leo elit tellus sapien arcu congue sit malesuada id.</p>
<p class="body-text" style="left:151px;top:1472px;width:330px;color:#d3d8e6">Vestibulum augue tempus sed scelerisque at tellus. Diam magna commodo donec odio. Quisque eget ridiculus risus placerat fringilla congue sit dolor. Penatibus massa urna egestas velit in tortor nec molestie tincidunt.</p>
<div class="btn" style="left:151px;top:1558px;width:131px;border-color:var(--white);color:var(--white)">Mehr erfahren <svg viewBox="0 0 14 10"><path d="M0 5h12M8 1l4 4-4 4" stroke="currentColor" fill="none"/></svg></div>
<div class="photo" style="left:610px;top:1256px;width:590px;height:484px;background:linear-gradient(135deg,#c9d2dc,#8c99aa 45%,#2f3b55);clip-path:polygon(0 0,100% 0,100% 100%,8% 100%,0 90%)" role="img" aria-label="Foto: Facharbeiter bedient eine Drehmaschine"></div>

<!-- Facts -->
<div class="eyebrow" style="left:151px;top:1792px">Fakten und Zahlen</div>
<h2 class="heading" style="left:151px;top:1810px">VALKORIN in Zahlen</h2>
<div class="rule-light" style="left:540px;top:1824px;width:495px"></div>
<div class="num" style="left:148px;top:1890px">22</div>
<div class="num-label" style="left:148px;top:1972px">JAHRE EXPERTISE</div>
<div class="vdiv" style="left:351px"></div>
<div class="num" style="left:364px;top:1890px">1.400</div>
<div class="num-label" style="left:364px;top:1972px">M² PRODUKTIONSFLÄCHE</div>
<div class="vdiv" style="left:580px"></div>
<div class="num" style="left:594px;top:1890px">20</div>
<div class="num-label" style="left:594px;top:1972px">ENGAGIERTE MITARBEITER</div>
<div class="vdiv" style="left:808px"></div>
<div class="num" style="left:844px;top:1890px">100%</div>
<div class="num-label" style="left:844px;top:1972px">MADE IN GERMANY</div>

<!-- News -->
<div class="eyebrow" style="left:151px;top:2111px">Neuigkeiten rund um die Metallverarbeitung</div>
<h2 class="heading" style="left:151px;top:2129px">Aktuelles &amp; Neuigkeiten</h2>
<div class="rule-light" style="left:475px;top:2143px;width:450px"></div>
<div class="abs" style="left:958px;top:2125px;width:40px;height:40px;border:1px solid #dfe3ea;display:flex;align-items:center;justify-content:center"><svg width="14" height="10" viewBox="0 0 14 10"><path d="M14 5H2M6 1L2 5l4 4" stroke="#9aa0ab" fill="none"/></svg></div>
<div class="abs" style="left:1008px;top:2125px;width:40px;height:40px;background:#c9dcf5;display:flex;align-items:center;justify-content:center"><svg width="14" height="10" viewBox="0 0 14 10"><path d="M0 5h12M8 1l4 4-4 4" stroke="#2d6fcf" fill="none"/></svg></div>

<div class="photo" style="left:151px;top:2200px;width:286px;height:210px;background:linear-gradient(150deg,#2c2f36,#a0683a 60%,#3a3c42);clip-path:polygon(0 0,92% 0,100% 10%,100% 100%,0 100%)" role="img" aria-label="Foto: Laserschneidanlage bei der Arbeit"></div>
<div class="photo" style="left:457px;top:2200px;width:286px;height:210px;background:linear-gradient(110deg,#3a3f47,#c8cdd4 50%,#5a6069);clip-path:polygon(0 0,92% 0,100% 10%,100% 100%,0 100%)" role="img" aria-label="Foto: geschwungene Metalllamellen"></div>
<div class="photo" style="left:763px;top:2200px;width:286px;height:210px;background:linear-gradient(110deg,#7b8594,#cfd5dd 50%,#8f99a6);clip-path:polygon(0 0,92% 0,100% 10%,100% 100%,0 100%)" role="img" aria-label="Foto: gefaltete Metallfassade"></div>
<div class="tag" style="left:151px;top:2427px">Categorytag</div>
<div class="tag" style="left:457px;top:2427px">Categorytag</div>
<div class="tag" style="left:763px;top:2427px">Categorytag</div>
<div class="news-title" style="left:151px;top:2460px">LOREM IPSUM DOLOR SIT AMET</div>
<div class="news-title" style="left:457px;top:2460px">LOREM IPSUM DOLOR SIT AMET</div>
<div class="news-title" style="left:763px;top:2460px">LOREM IPSUM DOLOR SIT AMET</div>
<div class="news-date" style="left:151px;top:2484px">vom 24. September 2023</div>
<div class="news-date" style="left:457px;top:2484px">vom 24. September 2023</div>
<div class="news-date" style="left:763px;top:2484px">vom 24. September 2023</div>
<div class="btn" style="left:512px;top:2536px;width:154px;border-color:var(--royal);color:var(--royal)">Alle News ansehen <svg viewBox="0 0 14 10"><path d="M0 5h12M8 1l4 4-4 4" stroke="currentColor" fill="none"/></svg></div>

<!-- Partner -->
<div class="rule-light" style="left:151px;top:2710px;width:885px"></div>
<div class="abs" style="left:1036px;top:2702px;color:#c9cdd5;font-size:10px">×</div>
<div class="eyebrow" style="left:151px;top:2772px">Partnerunternehmen</div>
<h2 class="heading" style="left:151px;top:2790px">Industrie- und Anlagenservice</h2>
<p class="body-text" style="left:151px;top:2836px;width:510px;color:var(--royal)">Lorem ipsum dolor sit amet consectetur. Risus risus dui commodo posuere aenean ac mauris sed. Morbi aliquam tincidunt nibh leo. Quam ipsum sapien mauris pharetra id convallis ac nunc venenatis. Blandit viverra nunc enim sagittis accumsan habitant. Leo elit tellus sapien arcu congue sit malesuada id.</p>
<div class="abs" style="left:792px;top:2828px;display:flex;align-items:center;gap:10px">
  <span style="width:26px;height:26px;background:var(--royal);display:block"></span>
  <span style="font-size:19px;font-weight:500;color:var(--royal);letter-spacing:.4px">Norda Anlagenservice</span>
</div>

<!-- Contact -->
<div class="abs" style="left:151px;top:3022px;width:1049px;height:373px;background:var(--royal)"></div>
<div class="abs" style="left:590px;top:3395px;width:610px;height:130px;background:var(--navy)"></div>
<div class="footer abs"></div>
<div class="photo" style="left:0;top:3120px;width:590px;height:508px;background:linear-gradient(135deg,#e6e9ee,#9aa6b6 45%,#233057);clip-path:polygon(0 0,90% 0,100% 12%,100% 100%,0 100%)" role="img" aria-label="Foto: Techniker mit Schutzhelm am Bedienpult einer Maschine"></div>
<h2 class="contact-line" style="left:667px;top:3128px;font-size:25px;font-weight:500">Kontakt</h2>
<div class="contact-line" style="left:667px;top:3160px;font-size:11px;color:#c6d3ee">So erreichen Sie uns</div>
<svg class="abs" style="left:667px;top:3236px" width="20" height="20" viewBox="0 0 20 20" fill="none" stroke="#9fb9e8" stroke-width="1.3"><path d="M5 2l3 4-2 2c1 2 4 5 6 6l2-2 4 3-2 3C9 18 2 11 2 4z"/></svg>
<div class="contact-line" style="left:699px;top:3226px;font-size:16px">+49 3000 / 555 020 00</div>
<div class="contact-line" style="left:699px;top:3248px;font-size:9px;color:var(--blue-soft);letter-spacing:1px">MO–FR &nbsp; 08:00 – 18:00</div>
<svg class="abs" style="left:667px;top:3303px" width="20" height="20" viewBox="0 0 20 20" fill="none" stroke="#9fb9e8" stroke-width="1.3"><path d="M2 9l16-7-5 16-3-6z M10 12l8-10"/></svg>
<div class="contact-line" style="left:699px;top:3293px;font-size:16px">info@valkorin-beispiel.de</div>
<div class="contact-line" style="left:699px;top:3316px;font-size:9px;color:var(--blue-soft)">Wir antworten meist binnen 24 Stunden</div>
<div class="abs" style="left:667px;top:3278px;width:382px;height:1px;background:#3a63a8"></div>
<div class="contact-line" style="left:667px;top:3443px;font-size:11px;line-height:15px">Oder nutzen Sie<br>unser <b style="font-weight:600">Kontaktformular</b></div>
<div class="btn" style="left:882px;top:3440px;width:167px;border-color:var(--white);color:var(--white)">Zum Kontaktformular <svg viewBox="0 0 14 10"><path d="M0 5h12M8 1l4 4-4 4" stroke="currentColor" fill="none"/></svg></div>

<!-- Footer -->
<div class="logo" style="left:151px;top:3755px;font-size:30px">VALKORIN</div>
<div class="fcol" style="left:151px;top:3818px;line-height:17px;width:270px">
  <b style="font-weight:600">Valkorin GmbH</b><br>
  <span style="color:#b5bbc7">Werkstraße 4<br>09390 Haldenau<br>Deutschland</span>
  <p style="margin-top:22px;color:#b5bbc7">Lorem ipsum dolor sit amet consectetur. Dolor cras eget a volutpat ullamcorper facilisis. Viverra aliquam ac aliquet aliquet odio in aliquet.</p>
</div>
<div class="fcol" style="left:455px;top:3745px">
  <h4>SEITEN</h4><p>Leistungen</p><p>Produkte</p><p>Fertigung</p><p>Qualifikation</p><p>Über uns</p>
</div>
<div class="fcol" style="left:608px;top:3745px">
  <h4>RECHTLICHES</h4><p>Impressum</p><p>Datenschutzerklärung</p>
  <h4 style="margin-top:30px">KONTAKT &amp; SONSTIGES</h4><p>FAQ</p><p>Kontakt</p><p>Links</p>
</div>
<div class="fcol" style="left:838px;top:3745px">
  <h4>KONTAKTINFORMATIONEN</h4>
  <p style="margin-bottom:4px">Telefon:</p><p style="color:var(--blue)">+49 3000 / 555 020 00</p>
  <p style="margin-bottom:4px;margin-top:20px">E-MAIL:</p><p style="color:var(--blue)">info@valkorin-beispiel.de</p>
</div>
<div class="btn" style="left:838px;top:3881px;width:80px;height:34px;border-color:var(--white);color:var(--white);border-radius:17px">Kontakt</div>
<div class="abs" style="left:151px;top:4000px;width:898px;height:1px;background:#262e3f"></div>
<div class="fcol" style="left:151px;top:4030px">Copyright © 2023 valkorin-beispiel.de</div>
<i class="sicon" style="left:843px"></i><i class="sicon" style="left:881px"></i><i class="sicon" style="left:919px"></i><i class="sicon" style="left:957px"></i><i class="sicon" style="left:995px"></i><i class="sicon" style="left:1033px"></i>

</body>
</html>
```